Poster Design Project

We are youth orchestra in Texas that is introducing a new summer program called: Weekend Bows Holiday Program (It's for students ages 8-18 who play already play violin/viola/cello/bass

Poster size: 11" by 17"

All the details are below, but on the poster we would need the website listed: www.marlowridgejuniorensemble.example and tell them to go to that website to apply online beginning April 1st

That's how we get business, they go to our website and apply. It also needs to say really big MRJE WEEKEND BOWS HOLIDAY PROGRAM

We want to use these posters every summer so no dates on it please. Only: April 1st is when we being accepting online applications (every year, so don't put a year) Also put: Camp is held on Saturdays in June and July with final concert, last Sunday in July

Also on the poster we need: Our goal is to keep young musicians playing over the summer –so don’t put your instrument away for the summer! Keep in shape by joining us for the Marlow Ridge Junior Ensemble’s summer program – Weekend Bows Holiday Program! Tuition is $225, which covers June/July Saturday rehearsals and the performance fee for the BVSD FAH concert, last Sunday in July.

I know we can't get all the info below on it, but I put it on so you could better understand what we are doing.

We have a logo already, that we have the rights to - I need something that kids/teens will think is cool looking and music related....we are string instruments only (violin, viola, cello, bass) we also want it to look classy looking, not cheap
I included 2 copies of the logo in different color set

here's all the details from our website:
Weekend Bows Holiday Program (June and July) - Tuition: $225

Rehearsals on Saturdays June &July with final concert on last Sunday in July @ BHS FAH

Our goal is to keep young musicians playing over the summer –so don’t put your instrument away for the summer! Keep in shape by joining us for the Marlow Ridge Junior Ensemble’s new summer program – Weekend Bows Holiday Program!

Tuition is $225, which covers June/July Saturday rehearsals and the performance fee for the BVSD FAH concert.

No audition is necessary. Enrollment is limited to the first 50 students in each age category, depending on instrumentation needs, so don’t delay – enrollment online begins April 1st. Siblings will receive a $50 discount, after the first child's regular priced tuition.

Weekend Bows I: Students entering grades 6 and below (3:00 – 4:20 P.M. )
Weekend Bows II: Students grades entering 7 and 8 (4:30 – 6:00 P.M.)
Weekend Bows III: Students entering grades 9-12 (6:15 – 7:45 P.M.)

Summer camp attendance policy is more lenient due to summer vacations. Please notify MRJE of summer absences as soon as your vacation/camp dates are known.

Target Market(s)

string players ages 10-18 and their parents

Industry/Entity Type

Business

Requirements
Must have
• Be able to see title from far, and prominently display how/when to apply and where (website)

Also only the concert is at BHS FAH, we rehearse at Harbel Music in Allen

I'm working on uploading files for our QR codes for website and phone - It's uploaded below
Nice to have
• If you have room, the Weekend Holiday Bows I II and III times/grades, etc. but doesn't have to be seen as prominently as the title and how to apply
Should not have
• pictures of violin/vla/cello/bass students if they look elementary aged, should be more in the teenager age group if you use pictures.

```html
<!DOCTYPE html>
<html lang="en">
<head>
<meta charset="utf-8">
<title>MRJE Weekend Bows Holiday Program</title>
<link rel="stylesheet" href="https://fonts.googleapis.com/css2?family=Questrial&family=Oswald:wght@300;500;600&family=Open+Sans:wght@400;700&display=swap">
<style>
  :root {
    --ink: #231f20;
    --white: #ffffff;
    --navy: #283891;
    --sky: #29abe2;
    --gold: #f7b21b;
    --sage: #9fc3a8;
    --text-grey: #333333;
    --rule-grey: #9a9a9a;
    --wood-dark: #5a2a10;
    --wood-mid: #9a4c1e;
    --wood-light: #b9652c;
  }
  * { box-sizing: border-box; margin: 0; padding: 0; }
  html, body { width: 945px; height: 1200px; overflow: hidden; }
  body { position: relative; font-family: "Open Sans", sans-serif; }

  .backdrop {
    position: absolute; inset: 0;
    background:
      radial-gradient(ellipse at 20% 15%, var(--wood-light) 0%, transparent 45%),
      radial-gradient(ellipse at 85% 80%, var(--wood-light) 0%, transparent 40%),
      linear-gradient(160deg, var(--wood-mid), var(--wood-dark) 55%, var(--wood-mid));
  }

  .poster {
    position: absolute; left: 105px; top: 31px;
    width: 738px; height: 1140px;
    background: var(--white);
  }
  .poster > * { position: absolute; }

  .brand {
    left: 0; right: 0; top: 48px;
    display: flex; justify-content: center; align-items: center; gap: 16px;
  }
  .brand-dot { width: 34px; height: 34px; border-radius: 50%; background: var(--sky); }
  .brand-name {
    font-family: "Questrial", sans-serif; font-size: 66px; line-height: 1;
    color: var(--ink); letter-spacing: 2px;
  }

  .hero { left: 0; top: 176px; width: 738px; height: 365px; background: var(--ink); }
  .hero > * { position: absolute; }
  .hero-title {
    left: 0; right: 0; top: 26px; text-align: center;
    font-family: "Questrial", sans-serif; font-weight: 400; font-size: 31px; color: var(--white);
    letter-spacing: 0.3px;
  }
  .apply-note {
    left: 45px; top: 92px;
    font-family: "Oswald", sans-serif; font-weight: 600; font-size: 25px; line-height: 32px;
    color: var(--gold);
  }
  .apply-date {
    left: 38px; top: 158px;
    font-family: "Oswald", sans-serif; font-weight: 600; font-size: 60px; line-height: 1;
    color: var(--sky); letter-spacing: -1px;
  }
  .concert-photo {
    left: 341px; top: 108px; width: 389px; height: 236px;
    border-radius: 90px 40px 110px 60px;
    background: linear-gradient(180deg, #8a5a3a 0%, #6b3e22 55%, #2a2222 100%);
    border: 6px solid var(--gold);
    border-left-color: var(--sky); border-top-color: var(--sage);
  }

  .intro { top: 557px; font-weight: 700; font-size: 12px; line-height: 17.5px; color: var(--navy); }
  .intro-goal { left: 33px; width: 338px; }
  .intro-fee { left: 395px; width: 320px; }
  .intro-fee strong { color: var(--navy); font-size: 13.5px; }
  .intro-divider { left: 380px; top: 560px; width: 1px; height: 62px; background: var(--rule-grey); }

  .schedule-note {
    left: 0; right: 0; top: 642px; text-align: center;
    font-family: "Oswald", sans-serif; font-weight: 300; font-size: 23px; color: var(--text-grey);
  }
  .fee-heading {
    left: 0; right: 0; top: 680px; text-align: center;
    font-family: "Oswald", sans-serif; font-weight: 600; font-size: 25px; color: var(--navy);
  }
  .rule {
    left: 22px; width: 694px; height: 2px;
    background: linear-gradient(90deg, transparent, var(--gold) 25%, var(--sage) 55%, var(--sky) 80%, transparent);
  }
  .rule-top { top: 731px; }
  .rule-bottom { top: 787px; }
  .dates {
    left: 0; right: 0; top: 747px; text-align: center;
    font-family: "Oswald", sans-serif; font-weight: 300; font-size: 20px; color: var(--text-grey);
  }

  .groups { left: 37px; top: 804px; width: 335px; }
  .group-name { font-weight: 700; font-size: 15px; color: var(--navy); margin-top: 6px; line-height: 22px; }
  .group-name:first-child { margin-top: 0; }
  .group-detail { font-size: 14.5px; line-height: 22px; color: var(--text-grey); }
  .groups-divider { left: 380px; top: 803px; width: 1px; height: 242px; background: var(--sky); }

  .facts { left: 397px; top: 829px; width: 310px; list-style: none; }
  .facts li {
    position: relative; padding-left: 16px; margin-bottom: 18px;
    font-weight: 700; font-size: 14px; line-height: 19px; color: var(--text-grey);
  }
  .facts li::before {
    content: ""; position: absolute; left: 0; top: 6px;
    width: 8px; height: 8px; border-radius: 50%; background: var(--sage);
  }
  .facts li.lead { font-size: 15.5px; line-height: 21px; }

  .footer {
    left: 0; top: 1063px; width: 738px; height: 77px; background: var(--ink);
    text-align: center; color: var(--white);
  }
  .footer-site { margin-top: 10px; font-weight: 700; font-size: 15px; }
  .footer-policy { margin-top: 8px; font-size: 10px; line-height: 14px; }
</style>
</head>
<body>
  <div class="backdrop" role="img" aria-label="Warm wood-grain texture background"></div>

  <main class="poster">
    <header class="brand">
      <span class="brand-dot"></span>
      <span class="brand-name">MRJE</span>
    </header>

    <section class="hero">
      <h1 class="hero-title">MRJE WEEKEND BOWS HOLIDAY PROGRAM</h1>
      <p class="apply-note">Accepting online<br>applications</p>
      <p class="apply-date">April 1st</p>
      <div class="concert-photo" role="img" aria-label="Photo of a youth string orchestra performing on stage with a conductor, framed in a violin-body outline"></div>
    </section>

    <p class="intro intro-goal">OUR GOAL is to keep young musicians playing over the summer –so don’t put your instrument away for the summer! Keep in shape by joining us for the Marlow Ridge Junior Ensemble’s summer program.</p>
    <div class="intro-divider"></div>
    <p class="intro intro-fee">Weekend Bows Holiday Program! Tuition is <strong>$225</strong>, which covers June/July Saturday rehearsals and the performance fee for the BVSD FAH concert, last Sunday in July.</p>

    <p class="schedule-note">[ Camp is held on Saturdays in June and July with final concert, last Sunday in July ]</p>
    <h2 class="fee-heading">Weekend Bows Holiday Program (June and July) - Tuition fees: $225</h2>

    <div class="rule rule-top"></div>
    <p class="dates">Rehearsals on Saturdays in June and July | with a concert on Sunday, 3 pm, last Sunday in July</p>
    <div class="rule rule-bottom"></div>

    <section class="groups">
      <h3 class="group-name">Weekend Bows I</h3>
      <p class="group-detail">Students grades 6 and below<br>(grade next school year with at least<br>1 year playing experience): 3:00 – 4:20 P.M.</p>
      <h3 class="group-name">Weekend Bows II</h3>
      <p class="group-detail">Students grades 7 and 8<br>(grade for next school yr.): 4:30 – 6:00 P.M.</p>
      <h3 class="group-name">Weekend Bows III</h3>
      <p class="group-detail">Students in grades 9-12<br>(grade for next school yr.): 6:15 – 7:45 P.M.</p>
    </section>
    <div class="groups-divider"></div>

    <ul class="facts">
      <li class="lead">No audition is necessary.</li>
      <li>Enrollment is limited to the first 50 students in each age category, depending on instrumentation needs, so don’t delay enrollment online begins April 1st.</li>
      <li class="lead">Siblings will receive a $50 discount, after the first child's regular priced tuition, every summer.</li>
    </ul>

    <footer class="footer">
      <p class="footer-site">Website:&nbsp; www.marlowridgejuniorensemble.example</p>
      <p class="footer-policy">Summer camp attendance policy is more lenient due to summer vacations. Please notify MRJE of summer absences<br>as soon as your vacation/camp dates are known.</p>
    </footer>
  </main>
</body>
</html>
```